Veltrano.co - Polar Expeditions Specialists

We need a modern, visually striking business card for Veltrano.co, a company specialized in selling expedition cruises to the most remote regions on Earth, with a focus on the Arctic and Antarctica. The design should instantly communicate that the cardholder is an expert in polar travel. Use clean, premium aesthetics with cool tones like icy blue and white, possibly incorporating polar imagery (ice, glaciers, penguins, etc.)

Attached the logo

Contact Information for Business Card

Feels high-end and trustworthy.. Visually memorable — encourages people to keep it

Colors
0054AA
0677BA
7BADD7
CADEEF
E8F1F8

Requirements
Must have
• ice, glaciers, penguins, montains
Nice to have
• modern, transparente,

```html
<!DOCTYPE html>
<html lang="en">
<head>
<meta charset="UTF-8">
<title>Veltrano.co – Business Card</title>
<link href="https://fonts.googleapis.com/css2?family=Poppins:wght@400;500;600;700&display=swap" rel="stylesheet">
<style>
  :root {
    --brand-blue: #2e78b8;
    --paper: #f0f0f0;
    --white: #ffffff;
    --ink: #1c1c1c;
    --stage: #e4e8ea;
    --emboss-light: rgba(255, 255, 255, 0.75);
    --emboss-shade: rgba(214, 216, 218, 0.55);
  }
  * { box-sizing: border-box; margin: 0; padding: 0; }
  html, body {
    width: 1200px; height: 960px; overflow: hidden;
    background: var(--stage);
    font-family: "Poppins", sans-serif;
  }
  .card {
    position: absolute; left: 250px; width: 702px; height: 400px;
    border-radius: 30px; overflow: hidden;
  }
  /* Front side */
  .card--front {
    top: 60px; background: var(--brand-blue); color: var(--white);
    text-align: center;
  }
  .front-mark {
    position: absolute; left: 50%; top: 62px; transform: translateX(-50%);
    width: 96px; height: 96px; border-radius: 50%; background: var(--white);
  }
  .front-wordmark {
    position: absolute; left: 0; right: 0; top: 180px;
    font-size: 74px; font-weight: 700; line-height: 1; letter-spacing: -0.5px;
  }
  .front-tagline {
    position: absolute; left: 0; right: 0; top: 272px;
    font-size: 23px; font-weight: 600;
  }
  /* Back side */
  .card--back {
    top: 501px; background: var(--paper);
    border: 4px solid var(--brand-blue);
    color: var(--ink);
  }
  .back-decoration {
    position: absolute; left: -20px; top: -10px; width: 470px; height: 420px;
    background:
      radial-gradient(ellipse 34% 30% at 14% 14%, var(--emboss-light) 0%, rgba(255,255,255,0) 100%),
      radial-gradient(ellipse 42% 52% at 42% 58%, var(--emboss-shade) 0%, rgba(220,222,224,0.25) 55%, rgba(240,240,240,0) 100%),
      radial-gradient(ellipse 50% 50% at 50% 50%, var(--emboss-light) 0%, rgba(255,255,255,0) 100%);
  }
  .back-brand { position: absolute; left: 344px; top: 22px; }
  .back-brand__mark {
    position: absolute; left: 0; top: 8px;
    width: 72px; height: 72px; border-radius: 50%; background: var(--brand-blue);
  }
  .back-brand__name {
    position: absolute; left: 96px; top: 0; white-space: nowrap;
    color: var(--brand-blue); font-size: 38px; font-weight: 700; line-height: 1.2;
  }
  .back-brand__tagline {
    position: absolute; left: 96px; top: 60px; white-space: nowrap;
    color: var(--brand-blue); font-size: 13px; font-weight: 600;
  }
  .holder {
    position: absolute; right: 20px; top: 168px; text-align: right;
  }
  .holder__name {
    color: var(--brand-blue); font-size: 32px; line-height: 1.1; white-space: nowrap;
  }
  .holder__first { font-weight: 600; }
  .holder__last { font-weight: 400; }
  .holder__title { font-size: 16px; font-weight: 500; margin-top: 2px; }
  .holder-bar {
    position: absolute; right: 0; top: 172px; width: 14px; height: 50px;
    background: var(--brand-blue);
  }
  .address {
    position: absolute; right: 20px; top: 240px; text-align: right;
    font-size: 16px; line-height: 23px; letter-spacing: 0.3px; font-style: normal;
  }
  .contacts {
    position: absolute; right: 20px; top: 310px; list-style: none;
    font-size: 16px; line-height: 23px; letter-spacing: 0.3px;
  }
  .contacts li { display: flex; justify-content: flex-end; align-items: center; gap: 8px; }
  .contacts svg { width: 15px; height: 15px; fill: var(--brand-blue); flex: none; }
</style>
</head>
<body>
  <section class="card card--front">
    <div class="front-mark"></div>
    <h1 class="front-wordmark">Veltrano.co</h1>
    <p class="front-tagline">Polar Expeditions Specialists</p>
  </section>

  <section class="card card--back">
    <div class="back-decoration" role="img" aria-label="Faint embossed polar bear with penguins and stars"></div>

    <div class="back-brand">
      <div class="back-brand__mark"></div>
      <div class="back-brand__name">Veltrano.co</div>
      <div class="back-brand__tagline">Polar Expeditions Specialists</div>
    </div>

    <div class="holder-bar"></div>
    <div class="holder">
      <h2 class="holder__name"><span class="holder__first">Marta</span> <span class="holder__last">Kelnerova</span></h2>
      <p class="holder__title">Founder &amp; CEO</p>
    </div>

    <address class="address">
      4180 Lakeshore Ave. Suite 310<br>
      Denton, TX 76201
    </address>

    <ul class="contacts">
      <li>(940) 555-0183
        <svg viewBox="0 0 24 24" aria-hidden="true"><path d="M6.6 10.8a15.1 15.1 0 0 0 6.6 6.6l2.2-2.2a1 1 0 0 1 1-.25 11.4 11.4 0 0 0 3.6.57 1 1 0 0 1 1 1V20a1 1 0 0 1-1 1A17 17 0 0 1 3 4a1 1 0 0 1 1-1h3.5a1 1 0 0 1 1 1c0 1.250.2 2.45.57 3.57a1 1 0 0 1-.25 1z"/></svg>
      </li>
      <li>info@veltrano.co
        <svg viewBox="0 0 24 24" aria-hidden="true"><path d="M2 5h20v14H2zm2 2v.4l8 5 8-5V7zm0 2.7V17h16V9.7l-8 5z"/></svg>
      </li>
      <li>www.veltrano.co
        <svg viewBox="0 0 24 24" aria-hidden="true"><path d="M12 2a10 10 0 1 0 0 20 10 10 0 0 0 0-20zm6.9 6h-3a15 15 0 0 0-1.4-3.9A8 8 0 0 1 18.9 8zM12 4c.8 1.2 1.5 2.5 1.9 4h-3.8c.4-1.5 1.1-2.8 1.9-4zM4.3 14a8 8 0 0 1 0-4h3.4a16 16 0 0 0 0 4zm.8 2h3a15 15 0 0 0 1.4 3.9A8 8 0 0 1 5.1 16zm3-8h-3a8 8 0 0 1 4.4-3.9A15 15 0 0 0 8.1 8zM12 20c-.8-1.2-1.5-2.5-1.9-4h3.8c-.4 1.5-1.1 2.8-1.9 4zm2.3-6H9.7a14 14 0 0 1 0-4h4.6a14 14 0 0 1 0 4zm.2 5.9a15 15 0 0 0 1.4-3.9h3a8 8 0 0 1-4.4 3.9zm1.8-5.9a16 16 0 0 0 0-4h3.4a8 8 0 0 1 0 4z"/></svg>
      </li>
    </ul>
  </section>
</body>
</html>
```